Landscape design build company door flyer

I would like this flyer to convey a high-level of professionalism for a company that is excellent with communication with their clients as well as a company that does incredible installations

Went on vacation/holiday

```html
<!DOCTYPE html>
<html lang="en">
<head>
<meta charset="utf-8">
<title>Cedarstone Builders – Outdoor Living Flyer</title>
<link href="https://fonts.googleapis.com/css2?family=Poppins:wght@400;500;600;700;800&display=swap" rel="stylesheet">
<style>
  :root{
    --navy:#0d2a40;
    --orange:#f26b0a;
    --paper:#e6e6e6;
    --stage:#efefef;
    --white:#ffffff;
    --ink:#1d2a36;
  }
  *{box-sizing:border-box;margin:0;padding:0}
  html,body{width:1200px;height:1029px;overflow:hidden;background:var(--stage)}
  body{font-family:"Poppins",sans-serif;position:relative}
  .flyer{position:absolute;left:215px;top:20px;width:770px;height:990px;background:var(--paper);overflow:hidden}
  .hero-photo{position:absolute;left:0;top:0}
  .brand{position:absolute;left:0;top:0;width:342px;height:168px;text-align:center}
  .brand-dot{width:58px;height:58px;border-radius:50%;background:var(--orange);margin:50px auto 0}
  .brand-name{font-weight:600;color:var(--orange);font-size:17px;letter-spacing:.5px;margin-top:6px;line-height:1.1;font-family:"Poppins",sans-serif}
  .brand-tag{font-size:8.5px;color:var(--navy);font-weight:500;letter-spacing:.3px;margin-top:2px}
  .headline{position:absolute;left:38px;top:222px;font-weight:800;font-size:55px;line-height:53px;letter-spacing:-1.2px;color:var(--white);text-transform:uppercase}
  .headline .accent{color:var(--orange);display:block}
  .project-photo{position:absolute;width:202px;height:202px;border-radius:50%;border:5px solid var(--white);top:416px}
  .project-photo.pavilion{left:47px;background:radial-gradient(circle at 45% 40%,#b8894f 0,#6f5a42 35%,#4f6a45 70%,#8aa3b8 100%)}
  .project-photo.deck{left:286px;background:linear-gradient(170deg,#9fb3c2 0,#6f7d6a 30%,#b4b8ba 55%,#8f9497 100%)}
  .project-photo.steps{left:522px;background:linear-gradient(160deg,#8c8c86 0,#a17a55 35%,#7e5c3e 60%,#b59b7a 100%)}
  .section-title{position:absolute;font-weight:700;font-size:25px;color:var(--navy);line-height:1}
  .section-title::after{content:"";position:absolute;left:0;top:31px;width:70px;height:3px;border-radius:2px;background:#f5a400}
  .about-title{left:38px;top:648px}
  .services-title{left:455px;top:648px}
  .about-text{position:absolute;left:38px;top:694px;width:348px;font-size:13.2px;line-height:15.7px;color:var(--ink);text-align:justify;hyphens:auto}
  .services-list{position:absolute;left:458px;top:693px;list-style:none}
  .services-list li{display:flex;align-items:center;height:22.3px;font-size:15px;font-weight:600;color:var(--navy)}
  .services-list svg{width:13px;height:13px;margin-right:16px;flex:none}
  .footer{position:absolute;left:0;top:892px;width:770px;height:98px}
  .footer svg.band{position:absolute;left:0;top:0}
  .phone-icon{position:absolute;left:37px;top:25px;width:51px;height:51px;background:var(--orange);display:flex;align-items:center;justify-content:center}
  .phone-number{position:absolute;left:98px;top:20px;font-weight:800;font-size:44px;letter-spacing:-1.5px;color:var(--white);line-height:60px}
  .contact{position:absolute;left:512px;font-size:15px;color:var(--white);display:flex;align-items:center}
  .contact svg{width:16px;height:16px;margin-right:13px}
  .contact.email{top:20px}
  .contact.web{top:45px}
</style>
</head>
<body>
<main class="flyer">
  <svg class="hero-photo" width="770" height="538" viewBox="0 0 770 538" role="img" aria-label="Photo of a two-storey house with a large wooden deck, railings and stairs above a lawn">
    <defs>
      <linearGradient id="heroTone" x1="0" y1="0" x2="1" y2="1">
        <stop offset="0" stop-color="#2f5f86"/>
        <stop offset=".5" stop-color="#25506f"/>
        <stop offset=".8" stop-color="#1f4a3c"/>
        <stop offset="1" stop-color="#2f6a3a"/>
      </linearGradient>
    </defs>
    <polygon points="403,0 770,0 770,538 0,538 0,168 317,168" fill="url(#heroTone)"/>
  </svg>

  <header class="brand">
    <div class="brand-dot"></div>
    <div class="brand-name">CEDARSTONE BUILDERS</div>
    <div class="brand-tag">OUTDOOR LIVING SPACES</div>
  </header>

  <h1 class="headline">Let’s create<br>your dream<span class="accent">outdoor living space!</span></h1>

  <div class="project-photo pavilion" role="img" aria-label="Photo of a covered pavilion with an outdoor kitchen"></div>
  <div class="project-photo deck" role="img" aria-label="Photo of a grey composite deck with black metal railing"></div>
  <div class="project-photo steps" role="img" aria-label="Photo of a brown wooden deck with wraparound steps"></div>

  <h2 class="section-title about-title">ABOUT US</h2>
  <p class="about-text">Discover the endless possibilities for your outdoor space with The Cedarstone Builders Team. Our team of skilled artisans is dedicated to turning your outdoor space into a breathtaking oasis that you’ll love coming home to. Whether it’s a cozy patio for intimate gatherings, a sprawling deck to host memorable parties, or a custom paver driveway that adds instant curb appeal, our high-quality craftsmanship ensures stunning results that exceed your expectations.</p>

  <h2 class="section-title services-title">OUR SERVICES</h2>
  <ul class="services-list">
    <li><svg viewBox="0 0 14 14"><circle cx="7" cy="7" r="7" fill="#f26b0a"/><path d="M3.8 7.2l2.2 2.1 4.2-4.4" stroke="#fff" stroke-width="1.8" fill="none" stroke-linecap="round" stroke-linejoin="round"/></svg>Paver Patios</li>
    <li><svg viewBox="0 0 14 14"><circle cx="7" cy="7" r="7" fill="#f26b0a"/><path d="M3.8 7.2l2.2 2.1 4.2-4.4" stroke="#fff" stroke-width="1.8" fill="none" stroke-linecap="round" stroke-linejoin="round"/></svg>Paver Driveways</li>
    <li><svg viewBox="0 0 14 14"><circle cx="7" cy="7" r="7" fill="#f26b0a"/><path d="M3.8 7.2l2.2 2.1 4.2-4.4" stroke="#fff" stroke-width="1.8" fill="none" stroke-linecap="round" stroke-linejoin="round"/></svg>Retaining Walls</li>
    <li><svg viewBox="0 0 14 14"><circle cx="7" cy="7" r="7" fill="#f26b0a"/><path d="M3.8 7.2l2.2 2.1 4.2-4.4" stroke="#fff" stroke-width="1.8" fill="none" stroke-linecap="round" stroke-linejoin="round"/></svg>Decks &amp; Railings</li>
    <li><svg viewBox="0 0 14 14"><circle cx="7" cy="7" r="7" fill="#f26b0a"/><path d="M3.8 7.2l2.2 2.1 4.2-4.4" stroke="#fff" stroke-width="1.8" fill="none" stroke-linecap="round" stroke-linejoin="round"/></svg>Pools</li>
    <li><svg viewBox="0 0 14 14"><circle cx="7" cy="7" r="7" fill="#f26b0a"/><path d="M3.8 7.2l2.2 2.1 4.2-4.4" stroke="#fff" stroke-width="1.8" fill="none" stroke-linecap="round" stroke-linejoin="round"/></svg>Outdoor Lighting</li>
    <li><svg viewBox="0 0 14 14"><circle cx="7" cy="7" r="7" fill="#f26b0a"/><path d="M3.8 7.2l2.2 2.1 4.2-4.4" stroke="#fff" stroke-width="1.8" fill="none" stroke-linecap="round" stroke-linejoin="round"/></svg>Firepits &amp; Fireplaces</li>
  </ul>

  <footer class="footer">
    <svg class="band" width="770" height="98" viewBox="0 0 770 98">
      <rect x="0" y="8" width="770" height="90" fill="#0d2a40"/>
      <polygon points="469,0 770,0 770,98 428,98" fill="#f26b0a"/>
    </svg>
    <div class="phone-icon">
      <svg width="28" height="28" viewBox="0 0 24 24"><path d="M6.6 10.8a15.1 15.1 0 0 0 6.6 6.6l2.2-2.2a1 1 0 0 1 1-.25 11.4 11.4 0 0 0 3.6.57 1 1 0 0 1 1 1V20a1 1 0 0 1-1 1A17 17 0 0 1 3 4a1 1 0 0 1 1-1h3.5a1 1 0 0 1 1 1c0 1.25.2 2.45.57 3.57a1 1 0 0 1-.25 1z" fill="#fff"/></svg>
    </div>
    <div class="phone-number">206-555-0148</div>
    <div class="contact email">
      <svg viewBox="0 0 24 24"><rect x="2" y="5" width="20" height="14" rx="1.5" fill="#fff"/><path d="M3 6l9 7 9-7" stroke="#f26b0a" stroke-width="1.8" fill="none"/></svg>
      info@cedarstonebuilders.com
    </div>
    <div class="contact web">
      <svg viewBox="0 0 24 24" fill="none" stroke="#fff" stroke-width="1.6"><circle cx="12" cy="12" r="9"/><ellipse cx="12" cy="12" rx="4" ry="9"/><path d="M3 12h18M5 7h14M5 17h14"/></svg>
      www.cedarstonebuilders.com
    </div>
  </footer>
</main>
</body>
</html>
```